World Wide News and Current Affairs website

We intends to start up a new website which deals on New and Current Affairs.
Attention Designers,
We want a home page design for this project. Our business is based in the United States. Our goal is to become a well known brand.
The website would consist of a category for News, Business and Tech.
The theme should be beautiful and attention seeking. The website would take bulk of it's news from the US, and Europe.
Designers can get inspiration from already existing new websites such as PWJ, KLV, DASKOLM.
All designs should be clean and easy to navigate.

```html
<!DOCTYPE html>
<html lang="en">
<head>
<meta charset="utf-8">
<title>XYZ — World News and Current Affairs</title>
<link rel="stylesheet" href="https://fonts.googleapis.com/css2?family=Lato:wght@400;700;900&display=swap">
<style>
:root{
  --red:#d0021b;
  --red-dark:#c40a12;
  --black:#111;
  --ink:#333;
  --muted:#666;
  --grey-bg:#e9e9e4;
  --white:#fff;
  --field:#ececec;
}
*{box-sizing:border-box;margin:0;padding:0}
html,body{width:1200px;height:2839px;overflow:hidden}
body{font-family:"Lato",Arial,sans-serif;color:var(--ink);background:var(--white);position:relative}
.abs{position:absolute}
.red{color:var(--red)}

/* nav */
.topnav{position:absolute;left:0;top:0;width:1200px;height:62px;background:var(--black)}
.brand{position:absolute;left:76px;top:0;width:123px;height:62px;display:flex;align-items:center;justify-content:center;gap:8px;color:var(--white);font-weight:900;font-size:34px;letter-spacing:1px}
.brand-dot{width:12px;height:12px;background:var(--red)}
.menu{position:absolute;left:286px;top:0;height:62px;display:flex}
.menu a{display:flex;align-items:center;padding:0 20px;height:62px;color:var(--white);text-decoration:none;font-size:16px;border-right:1px solid #444}
.menu a.active{border-bottom:3px solid var(--red)}
.search-ico{position:absolute;left:1100px;top:21px}

/* hero band */
.hero-band{position:absolute;left:0;top:62px;width:1200px;height:549px;background:var(--grey-bg)}
.welcome{position:absolute;left:78px;top:38px;font-size:28px;color:var(--black)}
.today{position:absolute;right:78px;top:42px;font-size:20px;color:var(--black)}
.hero{position:absolute;left:78px;top:84px;width:1044px;height:416px;background:linear-gradient(120deg,#5a6e94 0%,#2b3244 45%,#1b1d26 100%)}
.tag{display:inline-block;background:#f0262b;color:var(--white);font-weight:700;font-size:15px;padding:4px 14px}
.date{color:var(--white);font-size:14px;margin-top:12px}
.title{color:var(--white);font-size:32px;font-weight:700}
.hero .card{position:absolute;left:32px;top:204px;width:700px}
.hero .title{font-size:32px;margin-top:2px}
.hero p{color:#eee;font-size:15px;line-height:25px;margin-top:8px}
.play{position:absolute;width:62px;height:40px;border-radius:10px;background:#e3141b;display:flex;align-items:center;justify-content:center}

/* trending */
.trending{position:absolute;left:0;top:611px;width:1200px;height:76px;background:var(--white)}
.trend-label{position:absolute;left:78px;top:24px;width:137px;height:30px;background:#e92f2f;color:var(--white);font-weight:700;font-size:15px;display:flex;align-items:center;justify-content:center;gap:6px}
.trend-text{position:absolute;left:242px;top:27px;font-size:16px;font-weight:700;color:var(--ink)}
.arrow-btn{position:absolute;top:26px;width:28px;height:28px;border-radius:50%;border:2px solid #888;display:flex;align-items:center;justify-content:center}

/* latest */
.latest{position:absolute;left:0;top:687px;width:1200px;height:647px;background:var(--grey-bg)}
.sec-head{position:absolute;font-size:36px;color:var(--black)}
.tabs{position:absolute;right:78px;top:45px;display:flex;gap:30px;font-size:18px;color:var(--muted)}
.tabs .on{color:var(--black);border-bottom:3px solid var(--red);padding-bottom:6px}
.tile{position:absolute;overflow:hidden}
.tile .card{position:absolute;left:44px;bottom:22px}
.tile .title{font-size:31px}

/* subscribe + top stories */
.mid{position:absolute;left:0;top:1334px;width:1200px;height:468px;background:var(--white)}
.subscribe{position:absolute;left:78px;top:52px;width:333px;height:365px;background:var(--red);color:var(--white);text-align:center}
.subscribe h3{font-weight:400;font-size:36px;margin-top:30px;display:flex;align-items:center;justify-content:center;gap:14px}
.subscribe h3::before,.subscribe h3::after{content:"";width:46px;height:2px;background:var(--white)}
.subscribe p{font-size:15px;line-height:25px;margin-top:12px}
.sub-field{display:block;margin:16px auto 0;width:289px;height:40px;background:var(--white);color:#999;font-size:14px;text-align:left;padding:11px 22px}
.sub-btn{display:block;margin:16px auto 0;width:289px;height:40px;background:var(--black);color:var(--white);font-weight:900;font-size:21px;line-height:40px}
.story{position:absolute;left:452px;top:105px;width:670px;height:312px;background:linear-gradient(110deg,#3d4652 0%,#6f7780 55%,#2e3035 100%)}
.story .card{position:absolute;left:44px;top:110px;width:600px}
.story p{color:#eee;font-size:15px;line-height:25px;margin-top:6px}

/* video */
.videos{position:absolute;left:0;top:1802px;width:1200px;height:488px;background:var(--grey-bg)}
.vthumb{position:absolute;top:127px;width:333px;height:219px}
.vcap{position:absolute;top:366px;width:333px}
.vcap h4{color:#e02323;font-weight:400;font-size:18px}
.vcap p{color:var(--muted);font-size:15px;line-height:25px;margin-top:4px}

/* stay updated */
.stay{position:absolute;left:0;top:2290px;width:1200px;height:209px;background:var(--white)}
.stay-field{position:absolute;top:114px;height:40px;background:var(--field);color:#999;font-size:14px;padding:12px 22px}
.signup{position:absolute;left:617px;top:114px;width:131px;height:40px;background:var(--red);color:var(--white);font-weight:900;font-size:21px;text-align:center;line-height:40px}
.divider{position:absolute;left:768px;top:38px;width:1px;height:128px;background:#ddd}
.weather{position:absolute;left:789px;top:56px;font-size:17px;color:var(--black)}
.site-search{position:absolute;left:824px;top:110px;width:248px;height:32px;border:1px solid #ccc;font-size:13px;color:#999;padding:8px 12px}
.site-search-btn{position:absolute;left:1036px;top:110px;width:36px;height:32px;background:var(--black);display:flex;align-items:center;justify-content:center}

/* footer */
.footer{position:absolute;left:0;top:2499px;width:1200px;height:293px;background:var(--grey-bg)}
.fcol{position:absolute;top:38px}
.fcol h5{color:var(--red);font-weight:400;font-size:20px;margin-bottom:15px}
.fcol li{list-style:none;font-size:15px;color:var(--muted);line-height:33.5px}
.legal{position:absolute;left:0;top:2792px;width:1200px;height:47px;background:var(--red-dark);color:var(--white);font-size:15px}
.legal .copy{position:absolute;left:78px;top:15px}
.legal nav{position:absolute;right:78px;top:15px;display:flex}
.legal nav span{padding:0 10px;border-left:1px solid var(--white)}
.legal nav span:first-child{border-left:0}
</style>
</head>
<body>

<header class="topnav">
  <div class="brand"><span class="brand-dot"></span>XYZ</div>
  <nav class="menu">
    <a class="active">HOME</a><a>ABOUT US</a><a>NEWS</a><a>BUSINESS</a><a>TECHNOLOGY</a><a>VIDEO</a><a>MORE ▾</a>
  </nav>
  <svg class="search-ico" width="20" height="20" viewBox="0 0 20 20"><circle cx="8" cy="8" r="6" fill="none" stroke="#fff" stroke-width="2.5"/><line x1="12.5" y1="12.5" x2="18" y2="18" stroke="#fff" stroke-width="3"/></svg>
</header>

<section class="hero-band">
  <h1 class="welcome" style="font-weight:400"><span class="red">Welcome to</span> XYZ</h1>
  <div class="today">Saturday, 22 April</div>
  <div class="hero" role="img" aria-label="Photo of politicians applauding in front of a flag">
    <div class="play" style="left:538px;top:160px"><svg width="18" height="20"><polygon points="2,1 17,10 2,19" fill="#fff"/></svg></div>
    <div class="card">
      <span class="tag">News</span>
      <div class="date">▦ April 21st, 2017</div>
      <div class="title">News Title</div>
      <p>Lorem Ipsum is simply dummy text of the printing and typesetting industry. Lorem Ipsum has been the industry's standard dummy text ever since the 1500s, when an unknown printer took a galley of type and scrambled it to make a type specimen book.</p>
    </div>
  </div>
</section>

<section class="trending">
  <div class="trend-label">ϟ TRENDING</div>
  <div class="trend-text">News Title : Lorem Ipsum is simply dummy text of the printing and typesetting industry.</div>
  <div class="arrow-btn" style="left:1051px"><svg width="10" height="12"><polyline points="7,1 2,6 7,11" fill="none" stroke="#666" stroke-width="2"/></svg></div>
  <div class="arrow-btn" style="left:1094px;border-color:var(--red)"><svg width="10" height="12"><polyline points="3,1 8,6 3,11" fill="none" stroke="#d0021b" stroke-width="2"/></svg></div>
</section>

<section class="latest">
  <h2 class="sec-head" style="left:78px;top:44px;font-weight:400"><span class="red">All The</span> Latest News</h2>
  <div class="tabs"><span class="on">News</span><span>Business</span><span>Technology</span></div>

  <article class="tile" style="left:0;top:125px;width:293px;height:231px;background:linear-gradient(150deg,#2b3a5a,#151a26)" role="img" aria-label="Photo of a city skyline at night">
    <div class="card"><span class="tag">News</span><div class="date">▦ April 21st, 2017</div><div class="title">News Title</div></div>
  </article>
  <article class="tile" style="left:303px;top:125px;width:293px;height:231px;background:linear-gradient(150deg,#6b4a3a,#2a1f1c)" role="img" aria-label="Photo of colleagues working at a desk">
    <div class="card"><span class="tag">News</span><div class="date">▦ April 21st, 2017</div><div class="title">News Title</div></div>
  </article>
  <article class="tile" style="left:0;top:364px;width:293px;height:231px;background:linear-gradient(150deg,#2c5fa6,#16325c)" role="img" aria-label="Photo of a flag against blue sky">
    <div class="card"><span class="tag">News</span><div class="date">▦ April 21st, 2017</div><div class="title">News Title</div></div>
  </article>
  <article class="tile" style="left:303px;top:364px;width:293px;height:231px;background:linear-gradient(150deg,#8a8e94,#3a3d42)" role="img" aria-label="Photo of a businessman in a city">
    <div class="card"><span class="tag">News</span><div class="date">▦ April 21st, 2017</div><div class="title">News Title</div></div>
  </article>
  <article class="tile" style="left:604px;top:125px;width:596px;height:470px;background:linear-gradient(130deg,#4d6170,#1f3a4d 55%,#2a5a78)" role="img" aria-label="Photo of a hand using a cybersecurity tablet screen">
    <div class="card"><span class="tag">News</span><div class="date">▦ April 21st, 2017</div><div class="title">News Title</div></div>
  </article>
</section>

<section class="mid">
  <div class="subscribe">
    <h3>Subscribe</h3>
    <p>Get the recent popular stories<br>straight into your inbox</p>
    <div class="sub-field">Name</div>
    <div class="sub-field">E - Mail</div>
    <div class="sub-btn">SUBMIT</div>
  </div>
  <h2 class="sec-head" style="left:452px;top:50px;font-weight:400"><span class="red">Top</span> Stories</h2>
  <article class="story" role="img" aria-label="Photo of a businesswoman in an office">
    <div class="card">
      <span class="tag">News</span>
      <div class="date">▦ April 21st, 2017</div>
      <div class="title">News Title</div>
      <p>Lorem Ipsum is simply dummy text of the printing and typesetting industry. Lorem Ipsum has been the industry's standard dummy text ever since the 1500s, when an unknown printer took a galley of type and scrambled it to make a type.</p>
    </div>
  </article>
</section>

<section class="videos">
  <h2 class="sec-head" style="left:78px;top:50px;font-weight:400"><span class="red">Featured</span> video</h2>
  <div class="arrow-btn" style="left:1051px;top:56px;border-color:var(--red)"><svg width="10" height="12"><polyline points="7,1 2,6 7,11" fill="none" stroke="#d0021b" stroke-width="2"/></svg></div>
  <div class="arrow-btn" style="left:1094px;top:56px"><svg width="10" height="12"><polyline points="3,1 8,6 3,11" fill="none" stroke="#666" stroke-width="2"/></svg></div>

  <div class="vthumb" style="left:78px;background:linear-gradient(150deg,#5e4436,#201916)" role="img" aria-label="Video still of colleagues at a desk">
    <div class="play" style="left:136px;top:90px"><svg width="18" height="20"><polygon points="2,1 17,10 2,19" fill="#fff"/></svg></div></div>
  <div class="vthumb" style="left:433px;background:linear-gradient(130deg,#56687a,#22394d)" role="img" aria-label="Video still of a cybersecurity tablet">
    <div class="play" style="left:136px;top:90px"><svg width="18" height="20"><polygon points="2,1 17,10 2,19" fill="#fff"/></svg></div></div>
  <div class="vthumb" style="left:789px;background:linear-gradient(150deg,#8d9196,#393c40)" role="img" aria-label="Video still of a businessman in a city">
    <div class="play" style="left:136px;top:90px"><svg width="18" height="20"><polygon points="2,1 17,10 2,19" fill="#fff"/></svg></div></div>

  <div class="vcap" style="left:78px"><h4>Lorem Ipsum is simply text Dummy</h4><p>Lorem Ipsum is simply dummy text of the printing and typesetting industry.</p></div>
  <div class="vcap" style="left:433px"><h4>Lorem Ipsum is simply text Dummy</h4><p>Lorem Ipsum is simply dummy text of the printing and typesetting industry.</p></div>
  <div class="vcap" style="left:789px"><h4>Lorem Ipsum is simply text Dummy</h4><p>Lorem Ipsum is simply dummy text of the printing and typesetting industry</p></div>
</section>

<section class="stay">
  <h2 class="sec-head" style="left:78px;top:42px;font-weight:400"><span class="red">Stay</span> Updated</h2>
  <div class="stay-field" style="left:78px;width:259px">Name</div>
  <div class="stay-field" style="left:347px;width:259px">E - Mail</div>
  <div class="signup">SIGN UP</div>
  <div class="divider"></div>
  <div class="weather">London, United Kingdom
    <svg style="vertical-align:middle;margin:0 8px 0 16px" width="40" height="26" viewBox="0 0 40 26"><circle cx="24" cy="10" r="8" fill="#d0021b"/><ellipse cx="16" cy="17" rx="14" ry="7" fill="#d0021b"/></svg>10°</div>
  <div class="site-search">Search XYZ...</div>
  <div class="site-search-btn"><svg width="14" height="14" viewBox="0 0 20 20"><circle cx="8" cy="8" r="6" fill="none" stroke="#fff" stroke-width="3"/><line x1="12.5" y1="12.5" x2="18" y2="18" stroke="#fff" stroke-width="3"/></svg></div>
</section>

<footer class="footer">
  <div class="fcol" style="left:78px"><h5>News</h5><ul><li>News Title</li><li>News Title</li><li>News Title</li><li>News Title</li><li>News Title</li><li>News Title</li></ul></div>
  <div class="fcol" style="left:350px"><h5>Business</h5><ul><li>Business Title</li><li>Business Title</li><li>Business Title</li><li>Business Title</li><li>Business Title</li><li>Business Title</li></ul></div>
  <div class="fcol" style="left:620px"><h5>Technology</h5><ul><li>Technology Title</li><li>Technology Title</li><li>Technology Title</li><li>Technology Title</li><li>Technology Title</li><li>Technology Title</li></ul></div>
  <div class="fcol" style="left:891px"><h5>More...</h5><ul><li>Title</li><li>Title</li><li>Title</li><li>Title</li><li>Title</li><li>Title</li></ul></div>
</footer>

<div class="legal">
  <div class="copy">© <b>XYZ</b> - 2017. All Rights Reserved.</div>
  <nav><span>Site Feedback</span><span>Corrections</span><span>Advertising Guidelines</span><span>Terms of Use</span><span>Privacy Policy</span></nav>
</div>

</body>
</html>
```